SaaS Early tech startup business card design

Unique design for experience ecommerce platform company. the business cards will be used by executive members. conformance with color code is required.

```html
<!DOCTYPE html>
<html lang="en">
<head>
<meta charset="utf-8">
<title>Velto — Business Card</title>
<link rel="stylesheet" href="https://fonts.googleapis.com/css2?family=Lato:wght@300;400;700&display=swap">
<style>
  :root {
    --page-bg: #2b2523;
    --card-bg: #171717;
    --teal: #1fb59c;
    --teal-soft: #3cc6aa;
    --blue: #1478a8;
    --text-light: #d9d9d9;
    --rule: #5a5a5a;
  }
  * { box-sizing: border-box; margin: 0; padding: 0; }
  html, body {
    width: 1200px; height: 842px; overflow: hidden;
    background: var(--page-bg);
    font-family: "Lato", sans-serif;
  }
  .sheet {
    width: 1200px; height: 842px;
    display: flex; align-items: center; justify-content: center; gap: 50px;
  }
  .card {
    position: relative;
    width: 540px; height: 309px;
    background: var(--card-bg);
    box-shadow: 0 14px 30px rgba(0,0,0,.45);
    overflow: hidden;
  }

  /* Back side: contact details */
  .card-back .band {
    position: absolute; left: 0; right: 0;
    background: var(--teal-soft);
  }
  .card-back .band-top { top: 0; height: 11px; }
  .card-back .band-bottom { bottom: 0; height: 14px; }
  .details {
    position: absolute; inset: 0;
    display: flex; flex-direction: column; align-items: center; justify-content: center;
    text-align: center; color: var(--text-light);
  }
  .person-name {
    color: var(--teal); font-weight: 400; font-size: 19px; letter-spacing: .3px;
    text-transform: uppercase; line-height: 1;
  }
  .person-role { font-weight: 400; font-size: 14px; margin-top: 3px; }
  .divider { width: 210px; height: 1px; background: var(--rule); margin: 10px 0; }
  .contact-list { list-style: none; font-size: 14px; line-height: 1.32; font-weight: 300; text-align: left; }
  .contact-list .label { color: var(--teal); font-weight: 400; margin-right: 3px; }
  .address { font-size: 14px; line-height: 1.35; font-weight: 300; }

  /* Front side: brand */
  .brand-name {
    position: absolute; left: 0; right: 0; top: 50%;
    transform: translateY(-56%);
    text-align: center;
    color: var(--teal); font-weight: 700; font-size: 76px; letter-spacing: -1px;
  }
  .accent { position: absolute; }
  .accent-left { left: 0; top: 185px; }
  .accent-right { right: 0; top: 62px; }
</style>
</head>
<body>
<main class="sheet">
  <section class="card card-back" aria-label="Card back">
    <div class="band band-top" role="img" aria-label="Teal checkered edge band"></div>
    <div class="details">
      <h1 class="person-name">Daniel Reyes</h1>
      <p class="person-role">Managing Director</p>
      <div class="divider"></div>
      <ul class="contact-list">
        <li><span class="label">P:</span>044-555 218 730</li>
        <li><span class="label">M:</span>044-555 218 731</li>
        <li><span class="label">E:</span>hello@veltohq.com</li>
        <li><span class="label">W:</span>www.veltohq.com</li>
      </ul>
      <div class="divider"></div>
      <p class="address">48 Harbour Lane,<br>Northgate, 560218</p>
    </div>
    <div class="band band-bottom" role="img" aria-label="Teal checkered edge band"></div>
  </section>

  <section class="card card-front" aria-label="Card front">
    <svg class="accent accent-left" width="86" height="44" viewBox="0 0 86 44" role="img" aria-label="Teal and blue checkered accent block">
      <rect x="0" y="0" width="62" height="44" fill="var(--teal-soft)"/>
      <rect x="68" y="0" width="7" height="44" fill="var(--blue)"/>
      <rect x="79" y="0" width="7" height="44" fill="var(--blue)"/>
    </svg>
    <p class="brand-name">velto</p>
    <svg class="accent accent-right" width="78" height="40" viewBox="0 0 78 40" role="img" aria-label="Blue and teal checkered accent block">
      <rect x="0" y="0" width="6" height="40" fill="var(--blue)"/>
      <rect x="10" y="0" width="6" height="40" fill="var(--blue)"/>
      <rect x="22" y="0" width="56" height="40" fill="var(--teal-soft)"/>
    </svg>
  </section>
</main>
</body>
</html>
```